The most modern business card ever !!!

Our company call “Vendalo”. Vendalo is a technology company specialized in cruises solutions. Out main product is a platform to reserve cruises. This is a revolutionary platform that make easier to travel agencies and final users to reserve cruises across dozen companies like tibba, wernu, hpv, dgb, etc..We are a “start up”, with a young team of developers and we want to transmit it.. For it, we want something different, a modern business card that represent cruises and technology.. When someone receive this card, this person should say: wowww this is different… this is modern… this is a cruise related company..
- diferent, modern
- traditions business card

```html
<!DOCTYPE html>
<html lang="en">
<head>
<meta charset="utf-8">
<title>Vendalo — Business Card</title>
<link rel="stylesheet" href="https://fonts.googleapis.com/css2?family=Work+Sans:wght@400;500;600&display=swap">
<style>
  :root {
    --backdrop: #1f1f1f;
    --card-dark: #1b1b1b;
    --card-light: #ffffff;
    --ink: #1a1a1a;
    --accent: #1ea5e0;
    --white: #ffffff;
  }
  * { margin: 0; padding: 0; box-sizing: border-box; }
  html, body {
    width: 1200px; height: 900px; overflow: hidden;
    background: radial-gradient(circle at 60% 30%, #3a3a3a 0%, var(--backdrop) 70%);
    font-family: "Work Sans", Arial, sans-serif;
  }
  .stage {
    position: relative; width: 1200px; height: 900px;
  }
  .card {
    position: absolute; left: 290px;
    width: 620px; height: 354px;
  }
  .card-back {
    top: 66px;
    background: linear-gradient(135deg, #161616 0%, #2a2a2a 60%, #1c1c1c 100%);
    display: flex; align-items: center; justify-content: center;
  }
  .card-back .wordmark {
    color: var(--white); font-size: 86px; font-weight: 500; letter-spacing: 2px;
  }
  .card-front {
    top: 480px; background: var(--card-light); color: var(--ink);
  }
  .card-front .wordmark {
    position: absolute; right: 36px; top: 34px;
    font-size: 52px; font-weight: 500; color: var(--ink); letter-spacing: 1px;
  }
  .holder { position: absolute; left: 40px; top: 110px; }
  .holder-name {
    color: var(--accent); font-size: 27px; font-weight: 500;
    letter-spacing: 1.5px; text-transform: uppercase;
  }
  .holder-role { font-size: 16px; letter-spacing: 1px; margin-top: 2px; }
  .divider {
    position: absolute; left: 40px; right: 36px; top: 196px;
    height: 2px; background: var(--accent);
  }
  .contacts {
    position: absolute; left: 40px; top: 214px; list-style: none;
    font-size: 17px; letter-spacing: 1.2px; line-height: 30px;
  }
  .contacts li { display: flex; align-items: center; gap: 10px; }
  .contacts svg { width: 13px; height: 13px; flex: none; }
  .address {
    position: absolute; right: 36px; bottom: 24px; text-align: right;
    font-size: 17px; letter-spacing: 1.5px; line-height: 28px;
  }
</style>
</head>
<body>
<main class="stage">
  <section class="card card-back">
    <span class="wordmark">Vendalo</span>
  </section>

  <section class="card card-front">
    <span class="wordmark">Vendalo</span>

    <div class="holder">
      <p class="holder-name">Darien Solt</p>
      <p class="holder-role">Director</p>
    </div>

    <div class="divider"></div>

    <ul class="contacts">
      <li>
        <svg viewBox="0 0 16 16" aria-hidden="true"><path d="M4 1 L6 5 L4.5 6.5 Q6 10 9.5 11.5 L11 10 L15 12 L14 15 Q6 15 1 4 Z" fill="none" stroke="#1ea5e0" stroke-width="1.6" stroke-linejoin="round"/></svg>
        (514) 555-0148
      </li>
      <li>
        <svg viewBox="0 0 16 16" aria-hidden="true"><rect x="1" y="3" width="14" height="10" fill="none" stroke="#1ea5e0" stroke-width="1.6"/><path d="M1 3 L8 9 L15 3" fill="none" stroke="#1ea5e0" stroke-width="1.6"/></svg>
        info@vendalo.com.br
      </li>
      <li>
        <svg viewBox="0 0 16 16" aria-hidden="true"><circle cx="8" cy="8" r="7" fill="none" stroke="#1ea5e0" stroke-width="1.4"/><ellipse cx="8" cy="8" rx="3" ry="7" fill="none" stroke="#1ea5e0" stroke-width="1.2"/><path d="M1 8 H15 M2.5 4.5 H13.5 M2.5 11.5 H13.5" stroke="#1ea5e0" stroke-width="1.2"/></svg>
        www.vendalo.com.br
      </li>
    </ul>

    <address class="address" style="font-style:normal">
      214b Harlow Street,<br>
      Brenmouth, NZ, 8042
    </address>
  </section>
</main>
</body>
</html>
```